Calder Vossik - Cinematographer

NEED:
I'm looking for a sleek, professional, modern business card that will give give the recipient the impression that they can trust their production will go smoothly by hiring me. I will bring creativity and knowledge to their shoot, so that we can create powerful images.
I am looking for a card with a strong style and design ethos that could be expanded to a website and a full visual/graphic/design entity for me.
ABOUT ME:
I am a mid-twenties cinematographer, I work on music video, narrative short, commercial, and corporate projects. I blend the science and artistry of cameras and filmmaking to tell a story. I'm an artist, a technician, and a manager.
DESIGN:
I like sleek, simple design. Black, dark grays, white, dark navy, steel blues, I love cyan, but also cyan and red. I am not a fan of earthy tones. I generally prefer modern, san-serif fonts over serifs. My old logo was based on an aperture, a multi-blade device at the back of a lens that controls how much light passes through, but I made it with so many colors, that it doesn't necessarily lend itself to a specific color-scheme or design ethos. I liked that the aperture design provided a sense of the technical requirements of my job. I'm a fan of matte business cards, but am open to plenty of specialty print processes to make an outstanding card.
ATTACHED FILES:
My Old Rainbox Aperture Logo, plus a few designs I've tried playing around with, but am not tied to. I AM OPEN TO NEW DESIGNS, DO NOT FEEL TIED TO THIS.
**I've pulled my old logo down from the attached files, and instead attached other business cards I like, so as not to mislead you where I would like to go.
INFO:
Name: Calder Vossik
Job: Cinematographer
Email: ccvossik@lumenpost.net
Phone: 415.555.0193
Website: caldervossik.com
Updates
I'm adding some images of other cards that I like, and removing my old logo, since I'm looking for something new, and don't want that old logo to push anyone a certain direction.

```html
<!DOCTYPE html>
<html lang="en">
<head>
<meta charset="utf-8">
<title>Calder Vossik – Cinematographer Business Card</title>
<link rel="stylesheet" href="https://fonts.googleapis.com/css2?family=Lato:wght@400;700&display=swap">
<style>
  :root {
    --canvas: #ffffff;
    --ink-black: #000000;
    --paper: #ffffff;
    --rim-dark: #2a2a2a;
    --emblem-dark-a: #2e2e2e;
    --emblem-dark-b: #050505;
    --emblem-light-a: #e4e4e4;
    --emblem-light-b: #f7f7f7;
    --title-gray-front: #8a8a8a;
    --title-gray-back: #7a7a7a;
  }
  html, body {
    margin: 0;
    padding: 0;
    width: 1200px;
    height: 1038px;
    overflow: hidden;
    background: var(--canvas);
  }
  .sheet {
    display: block;
    width: 1200px;
    height: 1038px;
  }
  .card-name {
    font-family: "Lato", sans-serif;
    font-weight: 700;
    font-size: 36px;
  }
  .card-name--front { fill: var(--paper); }
  .card-name--back { fill: var(--ink-black); }
  .card-title {
    font-family: "Lato", sans-serif;
    font-weight: 400;
    font-size: 20px;
  }
  .card-title--front { fill: var(--title-gray-front); }
  .card-title--back { fill: var(--title-gray-back); }
  .card-contact {
    font-family: "Lato", sans-serif;
    font-weight: 400;
    font-size: 12.5px;
    fill: var(--ink-black);
  }
</style>
</head>
<body>
<svg class="sheet" viewBox="0 0 1200 1038" xmlns="http://www.w3.org/2000/svg" aria-label="Calder Vossik business card, front and back">
  <defs>
    <filter id="card-shadow" x="-20%" y="-20%" width="140%" height="140%">
      <feDropShadow dx="3" dy="4" stdDeviation="5" flood-color="#000" flood-opacity="0.35"/>
    </filter>
    <filter id="name-glow" x="-10%" y="-50%" width="120%" height="200%">
      <feGaussianBlur in="SourceAlpha" stdDeviation="2.5" result="blur"/>
      <feFlood flood-color="#ffffff" flood-opacity="0.7"/>
      <feComposite in2="blur" operator="in" result="glow"/>
      <feMerge><feMergeNode in="glow"/><feMergeNode in="SourceGraphic"/></feMerge>
    </filter>
    <radialGradient id="emblem-dark-fill" cx="35%" cy="35%" r="75%">
      <stop offset="0" stop-color="var(--emblem-dark-a)"/>
      <stop offset="1" stop-color="var(--emblem-dark-b)"/>
    </radialGradient>
    <radialGradient id="emblem-light-fill" cx="30%" cy="30%" r="75%">
      <stop offset="0" stop-color="var(--emblem-light-a)"/>
      <stop offset="1" stop-color="var(--emblem-light-b)"/>
    </radialGradient>
  </defs>

  <g class="card card--front">
    <circle cx="270" cy="235" r="208" fill="var(--paper)" filter="url(#card-shadow)"/>
    <g class="card-emblem" role="img" aria-label="Film leader emblem in black and dark gray">
      <circle cx="270" cy="235" r="197" fill="url(#emblem-dark-fill)"/>
    </g>
    <text class="card-name card-name--front" x="103" y="249" textLength="295" lengthAdjust="spacing" filter="url(#name-glow)">CALDER VOSSIK</text>
    <text class="card-title card-title--front" x="160" y="289" textLength="280" lengthAdjust="spacing">CINEMATOGRAPHER</text>
  </g>

  <g class="card card--back">
    <circle cx="270" cy="772" r="205" fill="var(--rim-dark)" filter="url(#card-shadow)"/>
    <g class="card-emblem" role="img" aria-label="Film leader emblem in light gray and white">
      <circle cx="270" cy="772" r="199" fill="url(#emblem-light-fill)"/>
    </g>
    <text class="card-name card-name--back" x="103" y="743" textLength="295" lengthAdjust="spacing" filter="url(#name-glow)">CALDER VOSSIK</text>
    <text class="card-title card-title--back" x="160" y="781" textLength="280" lengthAdjust="spacing">CINEMATOGRAPHER</text>
    <text class="card-contact" x="280" y="811">415.555.0193</text>
    <text class="card-contact" x="280" y="832">ccvossik@lumenpost.net</text>
    <text class="card-contact" x="280" y="852">www.caldervossik.com</text>
  </g>
</svg>
</body>
</html>
```